Dorian Vasko Consulting

I've the wording, and the rough layout. See attached MicroSoft Word File. I need a professional to make my postcard "look pretty".

Industry/Entity Type

Consulting

```html
<!DOCTYPE html>
<html lang="en">
<head>
<meta charset="utf-8">
<title>Dorian Vasko Consulting – Small Business Success Secrets</title>
<link rel="stylesheet" href="https://fonts.googleapis.com/css2?family=Roboto:wght@300;700&family=Arimo:wght@400&display=swap">
<style>
  :root {
    --brand-blue: #1f88b4;
    --figure-tone: #2590bd;
    --ink-white: #ffffff;
  }
  html, body {
    margin: 0;
    padding: 0;
    width: 1200px;
    height: 801px;
    overflow: hidden;
    background: var(--brand-blue);
  }
  .postcard {
    position: relative;
    width: 1200px;
    height: 801px;
    background: var(--brand-blue);
    overflow: hidden;
    color: var(--ink-white);
  }
  .headline {
    position: absolute;
    left: 60px;
    top: 70px;
    margin: 0;
    font-family: "Roboto", "Helvetica Neue", Arial, sans-serif;
    font-weight: 300;
    font-size: 57px;
    line-height: 70px;
    letter-spacing: -0.5px;
  }
  .headline strong {
    font-weight: 700;
  }
  .growth-chart {
    position: absolute;
    left: 0;
    top: 0;
    width: 1200px;
    height: 801px;
  }
  .chart-line {
    fill: none;
    stroke: var(--ink-white);
    stroke-width: 2.5;
    stroke-linejoin: round;
    stroke-linecap: round;
  }
  .chart-node {
    fill: var(--ink-white);
  }
  .climber-figure {
    fill: var(--figure-tone);
  }
  .body-copy {
    position: absolute;
    left: 590px;
    top: 425px;
    width: 576px;
    font-family: "Arimo", Arial, sans-serif;
    font-size: 17px;
    line-height: 29px;
    text-align: justify;
  }
  .body-copy p {
    margin: 0 0 29px;
  }
</style>
</head>
<body>
  <main class="postcard">
    <h1 class="headline">
      Learn <strong>Small Business</strong><br>
      <strong>Success</strong> Secrets<br>
      only <strong>“insiders”</strong><br>
      know about:
    </h1>

    <svg class="growth-chart" viewBox="0 0 800 534">
      <rect class="climber-figure" x="436" y="40" width="124" height="226" rx="6"
            role="img" aria-label="Outline illustration of a businessman with a briefcase striding up the growth line"/>
      <polyline class="chart-line" points="268,411 336,309 362,329 398,275 432,275 460,276 505,277 520,250 545,240 570,263 613,178 657,195 700,132"/>
      <polyline class="chart-line" points="686,132 700,130 697,144"/>
      <circle class="chart-node" cx="268" cy="411" r="6"/>
      <circle class="chart-node" cx="336" cy="309" r="6"/>
      <circle class="chart-node" cx="362" cy="329" r="6"/>
      <circle class="chart-node" cx="398" cy="275" r="6"/>
      <circle class="chart-node" cx="505" cy="277" r="6"/>
      <circle class="chart-node" cx="570" cy="263" r="6"/>
      <circle class="chart-node" cx="613" cy="178" r="6"/>
    </svg>

    <section class="body-copy">
      <p>“Insiders” who know the answers to these tricky business problems, get ahead in business and life. And the deeper their understanding to these tricky business problems, the more successful they become. They have very little stress from their businesses; they work very few hours by building their businesses into "auto pilot". They have more free time to enjoy life.</p>
      <p>If you don't know how to solve these tricky business problems, you will find yourself struggling with your businesses. You will find yourself working very long hours, and you have a lot of stress from running your business. If you are not even aware of the existence of this aspect of running a business, your business will not survive. You will become part of the statistic: 80% of businesses fail.</p>
    </section>
  </main>
</body>
</html>
```